Tech business card design

We need an amazing business card design for our new business 'Pexla' a marketing tech startup based in Sydney, Australia. We provide an online marketplace for businesses to search and buy advertising media, connect with service providers and learn more about marketing. We wish to communicate 'cool tech', reliability and professionalism and design based around our logo.

Target Market(s)

Business Owners

Contact Information for Business Card

Name
Position
Email Address
Website
Phone Number

Font styles to use
Other font styles liked:
• Avenir & Avenir Next

Colors

Designer to choose colors to be used in the design.

```html
<!DOCTYPE html>
<html lang="en">
<head>
<meta charset="utf-8">
<title>Pexla Business Card</title>
<link rel="stylesheet" href="https://fonts.googleapis.com/css2?family=Montserrat:wght@400;500;700;800&display=swap">
<style>
  :root {
    --backdrop: #1b1b1b;
    --card-dark: #111111;
    --card-light: #ffffff;
    --ink-navy: #1d1f3d;
    --ink-dark: #1a1a1a;
    --ink-muted: #4a4a4a;
    --text-light: #e6e6e6;
  }
  * { box-sizing: border-box; margin: 0; padding: 0; }
  html, body { width: 1200px; height: 1000px; overflow: hidden; }
  body {
    background: var(--backdrop);
    font-family: "Montserrat", "Avenir Next", sans-serif;
    position: relative;
  }
  .card {
    position: absolute;
    width: 620px;
    height: 354px;
    left: 290px;
    border-radius: 4px;
    box-shadow: 0 18px 40px rgba(0,0,0,.55);
  }
  .card-front { top: 90px; background: var(--card-dark); }
  .card-back { top: 520px; background: var(--card-light); }

  .front-wordmark {
    position: absolute;
    top: 110px;
    left: 0;
    width: 100%;
    text-align: center;
    font-weight: 800;
    font-size: 92px;
    letter-spacing: -2px;
    color: var(--text-light);
    line-height: 1;
  }
  .front-web {
    position: absolute;
    top: 250px;
    width: 100%;
    text-align: center;
    font-size: 13px;
    color: var(--text-light);
    letter-spacing: .3px;
  }

  .back-wordmark {
    position: absolute;
    left: 48px;
    top: 170px;
    font-weight: 800;
    font-size: 86px;
    letter-spacing: -2px;
    color: var(--ink-navy);
    line-height: 1;
  }
  .back-divider {
    position: absolute;
    left: 348px;
    top: 78px;
    width: 2px;
    height: 150px;
    background: var(--ink-navy);
  }
  .contact {
    position: absolute;
    left: 366px;
    top: 72px;
  }
  .contact-name {
    font-weight: 700;
    font-size: 20px;
    color: var(--ink-dark);
    line-height: 1.1;
  }
  .contact-role {
    font-size: 11px;
    color: var(--ink-muted);
    margin-bottom: 10px;
  }
  .contact-row {
    display: flex;
    align-items: center;
    gap: 8px;
    font-size: 13px;
    color: var(--ink-dark);
    margin-bottom: 7px;
  }
  .contact-icon {
    width: 22px;
    height: 22px;
    background: var(--ink-navy);
    border-radius: 3px;
    display: flex;
    align-items: center;
    justify-content: center;
  }
</style>
</head>
<body>
  <section class="card card-front">
    <div class="front-wordmark">pexla</div>
    <div class="front-web">www.pexlamedia.com.au</div>
  </section>

  <section class="card card-back">
    <div class="back-wordmark">pexla</div>
    <div class="back-divider"></div>
    <div class="contact">
      <div class="contact-name">Liam Carter</div>
      <div class="contact-role">Founder, Director</div>
      <div class="contact-row">
        <span class="contact-icon">
          <svg width="14" height="14" viewBox="0 0 24 24"><path fill="#fff" d="M6.6 10.8a15 15 0 0 0 6.6 6.6l2.2-2.2c.3-.3.7-.4 1-.2 1.1.4 2.3.6 3.6.6.6 0 1 .4 1 1V20c0 .6-.4 1-1 1A17 17 0 0 1 3 4c0-.6.4-1 1-1h3.5c.6 0 1 .4 1 1 0 1.3.2 2.5.6 3.6.1.3 0 .7-.2 1z"/></svg>
        </span>
        +61 (0)412 555 208
      </div>
      <div class="contact-row">
        <span class="contact-icon">
          <svg width="14" height="14" viewBox="0 0 24 24"><rect x="2" y="5" width="20" height="14" fill="none" stroke="#fff" stroke-width="2"/><path d="M2 5l10 8 10-8" fill="none" stroke="#fff" stroke-width="2"/></svg>
        </span>
        liam@pexlamedia.com.au
      </div>
      <div class="contact-row">
        <span class="contact-icon">
          <svg width="14" height="14" viewBox="0 0 24 24" fill="none" stroke="#fff" stroke-width="2"><circle cx="12" cy="12" r="9"/><path d="M3 12h18M12 3c3 3 3 15 0 18M12 3c-3 3-3 15 0 18"/></svg>
        </span>
        www.pexlamedia.com.au
      </div>
    </div>
  </section>
</body>
</html>
```